Website improvements and Adding Functionalities at https://mervo.site/tarnovex

1.Search functionality
2.Payment process functionality
3. Application configuration
4. Registration functionality activation
5. Chat functionality
6.Language switching functionality (Portuguese & French)
7.Bespoke interactive modules
8. Automated web scraping and data synchronisation mechanisms
9. News Page
10.Webinar facilities
11. Basic SEO optimisation
12. Speed and performance optimisation
13. Security configuration
14. Google Analytics integration
15. Cross-browser and mobile testing
16. Website deployment and launch support

Target Market(s)

My target markets are companies, investors, suppliers and professionals with an interest in the Mozambican oil and gas sector

Industry/Entity Type

Oil and Gas

Coding

Coded - Design and coding required

Number of Pages Required

1 page

Requirements
Must have
• Improve the existing page at https://mervo.site/tarnovex and add the following features to it: 1. Search functionality 2. Payment process functionality 3. Application configuration 4. Activation of registration functionality 5. Chat functionality 6. Language switching functionality (Portuguese & French) 7. Bespoke interactive modules 8. Automated web scraping and data synchronisation mechanisms 9. News Page

```html
<!DOCTYPE html>
<html lang="en">
<head>
<meta charset="utf-8">
<title>Tarnovex – Mozambique Oil &amp; Gas Intelligence</title>
<link rel="stylesheet" href="https://fonts.googleapis.com/css2?family=Oswald:wght@500;600;700&family=Inter:wght@400;500;600&display=swap">
<style>
:root{
  --red:#e23b1f;
  --red-dark:#c72f15;
  --navy:#1b1634;
  --navy-card:#241f40;
  --beige:#f2eee7;
  --ink:#16142a;
  --muted:#55536a;
  --white:#ffffff;
  --gold:#f4b41a;
}
*{box-sizing:border-box;margin:0;padding:0}
html,body{width:1200px;height:4096px;overflow:hidden}
body{font-family:"Inter",sans-serif;color:var(--ink);background:var(--white);position:relative}
.head{font-family:"Oswald",sans-serif;font-weight:600;text-transform:uppercase;letter-spacing:.2px}
.accent{color:var(--red)}
.btn{display:inline-block;background:var(--red);color:var(--white);font-family:"Inter",sans-serif;font-weight:600;font-size:14px;text-transform:uppercase;border-radius:8px;padding:11px 22px;text-decoration:none}
.btn-outline{background:var(--white);color:var(--red);border:2px solid var(--red)}
section{position:absolute;left:0;width:1200px;overflow:hidden}

/* header */
.site-header{top:0;height:175px;background:var(--white)}
.brand{position:absolute;left:160px;top:60px;display:flex;align-items:center;gap:12px}
.brand-dot{width:40px;height:40px;border-radius:50%;background:var(--navy)}
.brand-name{font-family:"Oswald",sans-serif;font-weight:600;font-size:24px;color:var(--ink);letter-spacing:2px}
.search{position:absolute;left:461px;top:32px;width:208px;height:40px;border-radius:8px;background:#ecebef;font-size:12px;color:#555;padding:12px 14px}
.search svg{position:absolute;right:12px;top:12px}
.top-actions{position:absolute;top:30px;left:690px;display:flex;gap:16px;align-items:center}
.top-actions .btn{padding:10px 20px;font-size:14px}
.lang{margin-left:12px;width:86px;height:42px;border-radius:8px;background:#ecebef;display:flex;align-items:center;justify-content:center;gap:8px;font-size:12px}
.lang i{width:18px;height:18px;border-radius:50%;background:linear-gradient(#b22 0 50%,#33a 50%)}
.nav{position:absolute;top:104px;left:436px;display:flex;gap:0;font-size:14px;font-weight:500}
.nav a{color:var(--ink);text-decoration:none;border-left:2px solid var(--gold);padding:0 16px;line-height:18px;text-transform:uppercase}
.nav a:last-child{border-left:none;padding-top:9px}

/* hero */
.hero{top:175px;height:525px;background:linear-gradient(100deg,#141a2a 0%,#23314d 45%,#2d4f86 70%,#1b2740 100%)}
.hero-photo{position:absolute;inset:0}
.hero-copy{position:absolute;left:159px;top:68px;width:430px;color:var(--white)}
.hero-copy h1{font-size:46px;line-height:47px}
.hero-copy p{margin-top:30px;font-size:13px;line-height:19px;width:360px}
.hero-copy .btn{margin-top:36px}
.dots{position:absolute;top:480px;left:563px;display:flex;gap:12px}
.dots i{width:8px;height:8px;border-radius:50%;background:var(--white)}
.dots i:first-child{background:var(--red)}

/* why */
.why{top:700px;height:473px;background:var(--white)}
.why-emblem{position:absolute;left:159px;top:85px;width:198px;height:305px;border-radius:24px;background:linear-gradient(180deg,#f5a623,#1b1634 45%)}
.glow{position:absolute;border-radius:50%;background:radial-gradient(circle,#fde7b8 0%,#fbd2b3 45%,rgba(255,255,255,0) 70%)}
.why h2{position:absolute;left:407px;top:85px;font-size:36px}
.squiggle{display:block;margin-bottom:8px}
.why-cols{position:absolute;left:407px;top:170px;display:flex}
.why-col{width:230px;padding-right:30px;border-right:1px solid #ddd;margin-right:0;padding-left:0}
.why-col+.why-col{padding-left:30px}
.why-col:last-child{border-right:none}
.why-col h3{font-size:17px;line-height:25px;margin:22px 0 20px}
.why-col p{font-size:12px;line-height:18px;color:var(--muted);width:160px}
.icon-red{width:50px;height:50px;border-radius:50%;border:5px solid var(--red);position:relative}
.icon-red::after{content:"";position:absolute;left:12px;top:12px;width:16px;height:16px;border-radius:50%;background:var(--red)}

/* access */
.access{top:1173px;height:824px;background:var(--navy);color:var(--white)}
.access h2{position:absolute;top:55px;width:100%;text-align:center;font-size:36px}
.access .squiggle{margin:0 auto 14px}
.grid{position:absolute;left:159px;top:190px;display:grid;grid-template-columns:repeat(3,283px);column-gap:15px;row-gap:14px}
.card{height:183px;background:var(--navy-card);border-radius:6px;padding:28px 28px}
.card .ic{width:42px;height:42px;border-radius:50%;background:var(--red);position:relative}
.card .ic::after{content:"";position:absolute;left:13px;top:13px;width:16px;height:16px;border-radius:3px;background:var(--white)}
.card h3{font-family:"Oswald",sans-serif;font-weight:500;font-size:16px;text-transform:uppercase;margin:24px 0 12px;line-height:21px}
.card p{font-size:12px;line-height:17px;color:#c9c6d8;width:220px}

/* about */
.about{top:1997px;height:503px;background:var(--beige)}
.about-gear{position:absolute;left:160px;top:60px;width:370px;height:370px;border-radius:50%;background:var(--navy)}
.about-photo{position:absolute;left:210px;top:110px;width:270px;height:270px;border-radius:50%;background:radial-gradient(circle at 50% 40%,#f0a35a 0%,#6a5b8f 45%,#2a3467 100%)}
.about-divider{position:absolute;left:587px;top:60px;width:1px;height:375px;background:#d9cfc0}
.about-copy{position:absolute;left:663px;top:60px;width:380px}
.about-copy h2{font-size:36px;margin-bottom:28px}
.about-copy p{font-size:13px;line-height:19px;color:#333;margin-bottom:18px}
.about-copy .btn{margin-top:12px}

/* insights */
.insights{top:2500px;height:743px;background:var(--white)}
.insights h2{position:absolute;top:60px;width:100%;text-align:center;font-size:36px}
.insights .squiggle{margin:0 auto 12px}
.posts{position:absolute;left:159px;top:202px;display:flex;gap:47px}
.post{width:262px;height:470px;border-radius:12px;background:var(--white);box-shadow:0 6px 24px rgba(20,20,40,.08);overflow:hidden}
.post-img{height:226px;border-radius:12px}
.post-body{padding:26px 28px}
.post h3{font-size:18px;line-height:24px;margin-bottom:16px}
.post p{font-size:11px;line-height:16px;color:#444;margin-bottom:18px}
.post .btn{font-size:11px;padding:8px 14px}

/* cta */
.cta{top:3243px;height:501px;background:linear-gradient(180deg,#1f3f8b 0%,#2a4d94 55%,#132654 100%)}
.cta-photo{position:absolute;left:520px;top:170px;width:360px;height:260px;border-radius:8px;background:radial-gradient(ellipse at 50% 60%,#f2904a 0%,#a25336 35%,rgba(30,40,90,0) 72%)}
.cta-copy{position:absolute;left:160px;top:60px;color:var(--white);width:420px}
.cta-copy h2{font-size:38px;line-height:41px;margin-bottom:26px}
.cta-copy p{font-size:14px;line-height:21px;width:340px}
.cta-btns{margin-top:40px;display:flex;gap:16px}
.cta-btns .btn{padding:12px 22px}
.chat{position:absolute;left:1082px;top:3712px;width:48px;height:48px;border-radius:50%;background:var(--navy);border:3px solid var(--red);z-index:5}
.chat svg{position:absolute;left:11px;top:11px}

/* footer */
.footer{top:3744px;height:352px;background:var(--beige)}
.footer .brand{top:70px;left:160px}
.fcols{position:absolute;left:426px;top:58px;display:flex;gap:0}
.fcol{margin-right:38px}
.fcol h4{font-family:"Oswald",sans-serif;font-weight:600;font-size:14px;text-transform:uppercase;margin-bottom:14px}
.fcol a{display:block;font-size:12px;line-height:24px;color:#333;text-decoration:none}
.fline{position:absolute;left:159px;top:228px;width:882px;height:1px;background:#d8d2c8}
.copy{position:absolute;top:287px;width:100%;text-align:center;font-size:12px;color:#333}
</style>
</head>
<body>

<section class="site-header">
  <div class="brand"><span class="brand-dot"></span><span class="brand-name">TARNOVEX CO</span></div>
  <div class="search">Search
    <svg width="14" height="14" viewBox="0 0 14 14"><circle cx="6" cy="6" r="4.5" fill="none" stroke="#555" stroke-width="1.5"/><path d="M9.5 9.5 13 13" stroke="#555" stroke-width="1.5"/></svg>
  </div>
  <div class="top-actions">
    <a class="btn" href="#">Register</a>
    <a class="btn btn-outline" href="#">Contact</a>
    <div class="lang"><i></i>EN ▾</div>
  </div>
  <nav class="nav">
    <a href="#">Industry<br>Insights</a>
    <a href="#">Oil &amp; Gas<br>Opportunities</a>
    <a href="#">Supplier &amp;<br>Company Network</a>
    <a href="#">Leagal<br>Framwork</a>
    <a href="#">News</a>
  </nav>
</section>

<section class="hero">
  <div class="hero-photo" role="img" aria-label="Engineer in hard hat operating a process control screen in an industrial plant"></div>
  <div class="hero-copy">
    <h1 class="head">Access Mozambique’s<br><span class="accent">Oil &amp; Gas Industry</span><br>Intelligence in One<br>Platform</h1>
    <p>Tarnovex is a modern online connection and consulting platform designed to facilitate access to the Mozambican Oil and Gas industry through premium industry insights, supplier information, tenders, legal frameworks, and strategic project data.</p>
    <a class="btn" href="#">Register Now</a>
  </div>
  <div class="dots"><i></i><i></i><i></i><i></i></div>
</section>

<section class="why">
  <div class="glow" style="left:-110px;top:320px;width:260px;height:260px"></div>
  <div class="why-emblem" role="img" aria-label="Brand emblem illustration"></div>
  <h2 class="head"><svg class="squiggle" width="52" height="20" viewBox="0 0 52 20"><path d="M2 16c6-12 10 4 16-6s10 6 16-4 10 6 16 2" fill="none" stroke="#222" stroke-width="2"/></svg>Why <span class="accent">Tarnovex</span> is Unique</h2>
  <div class="why-cols">
    <div class="why-col"><div class="icon-red"></div><h3 class="head">Up-to-Date Industry<br>Intelligence</h3><p>Receive frequent updates about developments in Mozambique’s Oil &amp; Gas sector.</p></div>
    <div class="why-col"><div class="icon-red"></div><h3 class="head">High-Quality<br>Curated Information</h3><p>Access carefully selected and synthesized information tailored to industry stakeholders.</p></div>
    <div class="why-col"><div class="icon-red"></div><h3 class="head">Time-Saving Access</h3><p style="width:180px">Avoid spending hours searching through scattered online sources with organized and accessible content in one platform.</p></div>
  </div>
</section>

<section class="access">
  <h2 class="head"><svg class="squiggle" width="52" height="20" viewBox="0 0 52 20"><path d="M2 16c6-12 10 4 16-6s10 6 16-4 10 6 16 2" fill="none" stroke="#fff" stroke-width="2"/></svg>What You Will <span class="accent">Access</span></h2>
  <div class="grid">
    <div class="card"><div class="ic"></div><h3>Hydrocarbon Industry<br>Information</h3><p>General information and insights about Mozambique’s oil and gas sector.</p></div>
    <div class="card"><div class="ic"></div><h3>Main Gas Projects</h3><p>Details about major gas and energy projects operating in Mozambique.</p></div>
    <div class="card"><div class="ic"></div><h3>Supplier &amp; Company Database</h3><p>Mozambican companies capable of meeting Level 3 supply requirements.</p></div>
    <div class="card"><div class="ic"></div><h3>Industry Contacts</h3><p>Key contacts from NOCs, Operators, EPCs, and Second-Tier Suppliers.</p></div>
    <div class="card"><div class="ic"></div><h3>Tender Opportunities</h3><p>Short, medium, and long-term tenders within the industry.</p></div>
    <div class="card"><div class="ic"></div><h3>Ownership &amp; Access</h3><p>Information related to hydrocarbon reserves and sector participation.</p></div>
    <div class="card"><div class="ic"></div><h3>Legal Framework</h3><p>Mozambican local content regulations and legal structures.</p></div>
    <div class="card"><div class="ic"></div><h3>Local Company Capacity</h3><p>Business integration opportunities within the oil and gas sector.</p></div>
    <div class="card"><div class="ic"></div><h3>Tender Application Guidance</h3><p>Support and information on applying for industry tenders.</p></div>
  </div>
</section>

<section class="about">
  <div class="about-gear"></div>
  <div class="about-photo" role="img" aria-label="Offshore oil platform at dusk"></div>
  <div class="about-divider"></div>
  <div class="about-copy">
    <h2 class="head"><svg class="squiggle" width="52" height="20" viewBox="0 0 52 20"><path d="M2 16c6-12 10 4 16-6s10 6 16-4 10 6 16 2" fill="none" stroke="#222" stroke-width="2"/></svg>What is <span class="accent">Tarnovex?</span></h2>
    <p>Tarnovex is a unique online platform built to connect businesses, investors, suppliers, and professionals with valuable information about the Mozambican Oil &amp; Gas sector.</p>
    <p>Through a secure digital paywall system, users gain access to organized, up-to-date, and carefully selected industry information that supports better decision-making, market understanding, and business opportunities within Mozambique’s growing hydrocarbons industry.</p>
    <a class="btn" href="#">Read More</a>
  </div>
</section>

<section class="insights">
  <h2 class="head"><svg class="squiggle" width="52" height="20" viewBox="0 0 52 20"><path d="M2 16c6-12 10 4 16-6s10 6 16-4 10 6 16 2" fill="none" stroke="#222" stroke-width="2"/></svg>Industry <span class="accent">Insights</span></h2>
  <div class="posts">
    <article class="post"><div class="post-img" role="img" aria-label="Offshore drilling rig under a pink sunset sky" style="background:linear-gradient(180deg,#3d78b8,#b58aa8 60%,#2c4f78)"></div>
      <div class="post-body"><h3 class="head">Mozambican Legal Framework for Local Content</h3><p>The existing legal framework in Mozambique relating to Local Content (LC) or LC issues is decentralized at the sectoral level</p><a class="btn" href="#">Read More</a></div></article>
    <article class="post"><div class="post-img" role="img" aria-label="Oil pump jack silhouetted against an orange sunset" style="background:linear-gradient(180deg,#f1a33a,#b85a12 60%,#3a1a08)"></div>
      <div class="post-body"><h3 class="head">Hydrocarbon – Geology, Exploration,Development and Production</h3><p>Hydrocarbons result from the transformation of organic matter, such as plants, animals and marine organisms, deposited in muddy</p><a class="btn" href="#">Read More</a></div></article>
    <article class="post"><div class="post-img" role="img" aria-label="Workers in orange coveralls walking beside white storage tanks" style="background:linear-gradient(180deg,#6da1d8,#cfd9e2 55%,#8a8f94)"></div>
      <div class="post-body"><h3 class="head">Petroleum Operations Regulation</h3><p>Since there is a need to define the modalities, terms and conditions of contracts, petroleum operations practices, including:<br>Resource management<br>Safety</p><a class="btn" href="#">Read More</a></div></article>
  </div>
</section>

<section class="cta">
  <div class="cta-photo" role="img" aria-label="Illuminated offshore rig on the sea at twilight"></div>
  <div class="cta-copy">
    <h2 class="head"><svg class="squiggle" width="52" height="20" viewBox="0 0 52 20"><path d="M2 16c6-12 10 4 16-6s10 6 16-4 10 6 16 2" fill="none" stroke="#fff" stroke-width="2"/></svg>Start Exploring Mozambique’s Oil &amp; Gas Opportunities</h2>
    <p>Register today to access premium industry information, supplier networks, tenders, and strategic market insights through Tarnovex.</p>
    <div class="cta-btns"><a class="btn" href="#">Register Now</a><a class="btn" href="#">Contact Us</a></div>
  </div>
</section>

<div class="chat"><svg width="20" height="20" viewBox="0 0 20 20"><path d="M10 2C5 2 1.5 5 1.5 9c0 2 1 3.8 2.6 5l-.8 3.5 3.8-2c1 .3 1.9.4 2.9.4 5 0 8.5-3 8.5-6.9S15 2 10 2z" fill="#fff"/><circle cx="6.5" cy="9" r="1.2" fill="#1b1634"/><circle cx="10" cy="9" r="1.2" fill="#1b1634"/><circle cx="13.5" cy="9" r="1.2" fill="#1b1634"/></svg></div>

<footer>
<section class="footer">
  <div class="glow" style="left:-80px;top:180px;width:300px;height:300px"></div>
  <div class="glow" style="left:1040px;top:230px;width:200px;height:200px"></div>
  <div class="brand"><span class="brand-dot"></span><span class="brand-name">TARNOVEX CO</span></div>
  <div class="fcols">
    <div class="fcol"><h4>Industry <span class="accent">Insights</span></h4><a href="#">Local Content Legal Framework</a><a href="#">Hydrocarbons Information</a><a href="#">O&amp;G Ownership &amp; Access</a><a href="#">Mozambican Oil &amp; gas books</a></div>
    <div class="fcol"><h4><span class="accent">Oil &amp; Gas</span> Opportunities</h4><a href="#">Oil and Gas tenders</a><a href="#">Tenders - short to long term</a><a href="#">Main Gas Projects Details</a></div>
    <div class="fcol"><h4><span class="accent">Supplier &amp; Company</span> Netowrk</h4><a href="#">Local Companies Capacity</a><a href="#">Moz Level 3 Suppliers List</a><a href="#">NOC, MNCs, EPCs &amp; II-Tier Suppliers</a></div>
  </div>
  <div class="fline"></div>
  <p class="copy">© 2026 by Tarnovex Co. All Rights Reserved.</p>
</section>
</footer>

</body>
</html>
```